Real Estate Website

I am looking for a website design for a website that will be featuring real estate listings across Australia. It will be a website for a real estate agency that operates through all states in Australia.

We like the designs of https://www.brightnest.com.au/ and https://valtoria.example/

On the brightnest website, we like the sell, buy, sold tabs but would also like lease, and agents. We also need a button somewhere for 'Join Agent Pivola' and 'Login'

On the Valtoria site it has a concierge section and we want something like that on the home page.

The contact details to show in the footer are:

Shop 2217B
Level 1 Harbourgate Shopping Centre
87 Quillon Terrace
Southport

Attached are various versions of the logo and some intro text to go on the home page.

```html
<!DOCTYPE html>
<html lang="en">
<head>
<meta charset="utf-8">
<title>Agent Pivola — Australia-Wide Real Estate</title>
<link href="https://fonts.googleapis.com/css2?family=Montserrat:wght@500;600;700&family=Mulish:wght@400;500;600;700&display=swap" rel="stylesheet">
<style>
:root{
  --gold:#a27c33;
  --brown:#8a5a1f;
  --tab-yellow:#efe58a;
  --pale-yellow:#fdfbdc;
  --ink:#1d1d1d;
  --muted:#444;
  --soft-bg:#f3f1f3;
  --white:#fff;
  --footer:#0d0b0a;
  --line:#e4e2e4;
}
*{margin:0;padding:0;box-sizing:border-box}
html,body{width:1200px;height:3817px;overflow:hidden}
body{position:relative;font-family:"Mulish",sans-serif;color:var(--ink);background:var(--white)}
.abs{position:absolute}
h1,h2,h3,.heading{font-family:"Montserrat",sans-serif;font-weight:700}

/* hero */
.hero{left:0;top:0;width:1200px;height:628px;background:linear-gradient(180deg,#4b6f9a 0%,#7e97b5 30%,#c9a88a 52%,#d8a877 62%,#5d5a62 72%,#3b4a5c 86%,#2d4a66 100%)}
.hero-shade{left:0;top:0;width:1200px;height:628px;background:linear-gradient(180deg,rgba(10,20,40,.35),rgba(10,20,40,.1) 50%,rgba(0,0,0,0))}
.brand{left:150px;top:110px;color:var(--white);font-family:"Mulish",sans-serif;font-weight:500;font-size:19px;letter-spacing:3.5px}
.brand-mark{left:214px;top:30px;width:50px;height:50px;border:2px solid var(--white);border-radius:50%}
.nav a{position:absolute;top:36px;color:var(--white);font-size:15px;text-decoration:none}
.nav .active::after{content:"";position:absolute;left:0;right:0;top:24px;height:2px;background:var(--white)}
.btn-join{left:816px;top:27px;width:142px;height:40px;background:var(--tab-yellow);color:var(--ink);font-size:14px;display:flex;align-items:center;justify-content:center}
.btn-login{left:973px;top:27px;width:75px;height:40px;border:1px solid var(--white);color:var(--white);font-size:14px;display:flex;align-items:center;justify-content:center}
.hero-title{left:0;width:1200px;top:190px;text-align:center;color:var(--white);font-size:34px}
.hero-sub{left:0;width:1200px;top:246px;text-align:center;color:var(--white);font-size:18px}
.search-tabs{left:181px;top:323px;width:222px;height:40px;background:#3b3430;display:flex}
.search-tabs span{color:var(--white);font-size:16px;display:flex;align-items:center;justify-content:center}
.search-tabs .on{background:var(--tab-yellow);color:var(--ink);width:84px}
.search-input{left:181px;top:363px;width:607px;height:47px;background:var(--white);font-size:12px;color:#333;padding-left:22px;display:flex;align-items:center}
.search-btn{left:788px;top:363px;width:239px;height:47px;background:var(--brown);color:var(--white);font-size:13px;font-weight:700;display:flex;align-items:center;justify-content:center;letter-spacing:.3px}

/* sections */
.soft{background:var(--soft-bg)}
.section-title{font-size:31px;color:var(--ink)}
.rule{height:2px;width:44px;background:var(--brown)}
.tabs span{position:absolute;top:694px;font-size:15px;color:var(--ink)}
.tabs .on{color:var(--gold)}
.tabs .on::after{content:"";position:absolute;left:0;right:0;top:24px;height:1px;background:var(--gold)}

.card{top:779px;width:287px;height:387px;background:var(--white);box-shadow:0 2px 8px rgba(0,0,0,.1)}
.card .photo{position:absolute;left:0;top:0;width:287px;height:214px}
.card .badge{position:absolute;left:6px;top:20px;background:var(--gold);color:var(--white);font-size:10px;font-weight:700;padding:3px 7px}
.card .price{position:absolute;left:29px;top:237px;color:var(--gold);font-size:19px;font-weight:700}
.card .addr{position:absolute;left:29px;top:269px;width:230px;font-size:14px;line-height:21px}
.card .feats{position:absolute;left:0;top:335px;width:287px;height:52px;border-top:1px solid var(--line);display:flex}
.card .feats div{display:flex;align-items:center;justify-content:center;gap:8px;font-size:13px;border-right:1px solid var(--line)}
.card .feats div:last-child{border-right:none}
.arrow{width:44px;height:44px;border:1.5px solid #888;border-radius:50%;display:flex;align-items:center;justify-content:center}
.btn-gold{background:var(--gold);color:var(--white);font-size:15px;display:flex;align-items:center;justify-content:center}

.city{top:1474px;width:136px;text-align:center}
.city .pic{width:136px;height:136px;border-radius:50%}
.city .name{font-size:15px;margin-top:28px}
.city .count{font-size:11px;margin-top:4px}
.divider{top:1603px;width:1px;height:71px;background:#cfcfcf}

.help{top:1951px;width:284px;height:350px;background:var(--white)}
.help.on{border:1px solid #a38d6e}
.help .art{position:absolute;left:36px;top:24px;width:186px;height:111px;border-radius:8px}
.help h3{position:absolute;left:36px;top:152px;font-size:17px}
.help p{position:absolute;left:36px;top:190px;width:220px;font-size:11px;line-height:16.5px}
.help .btn{position:absolute;left:36px;top:278px;height:34px;padding:0 22px;font-size:12px;font-weight:700;display:flex;align-items:center;border:2px solid var(--brown);color:var(--brown)}
.help.on .btn{background:var(--brown);color:var(--white)}

.concierge{left:0;top:2353px;width:1200px;height:437px;background:linear-gradient(90deg,#2f3a44 0%,#4a5156 40%,#6e6660 65%,#4d5a3a 100%)}
.concierge-shade{left:0;top:2353px;width:1200px;height:437px;background:linear-gradient(90deg,rgba(15,20,28,.55),rgba(15,20,28,.2) 60%,rgba(0,0,0,0))}
.c-title{left:148px;top:2398px;color:var(--white);font-size:37px;line-height:45px}
.c-q{left:150px;color:var(--white);font-size:18px;font-weight:700;font-family:"Mulish",sans-serif}
.c-text{left:150px;top:2620px;width:520px;color:var(--white);font-size:15px;line-height:22px}

.sell-box{left:28px;top:2837px;width:491px;height:479px;background:var(--pale-yellow)}
.sell-photo{left:519px;top:2892px;width:653px;height:507px;background:linear-gradient(135deg,#c9c2b8 0%,#e9e6df 45%,#a88b6a 75%,#f1efe9 100%)}
.sell-label{left:28px;top:2903px;width:491px;text-align:center;font-size:13px;font-weight:700;letter-spacing:.5px}
.sell-title{left:28px;top:2938px;width:491px;text-align:center;font-size:31px;line-height:44px;font-weight:600}
.sell-text{left:88px;top:3107px;width:371px;text-align:center;font-size:15px;line-height:22px}

footer{left:0;top:3453px;width:1200px;height:364px;background:var(--footer)}
.f-brand{left:150px;top:3620px;color:var(--gold);font-size:20px;letter-spacing:4px;font-weight:500}
.f-mark{left:228px;top:3512px;width:62px;height:62px;border:2px solid var(--gold);border-radius:50%}
.f-head{top:3500px;color:var(--gold);font-size:14px;font-weight:700}
.f-list{color:#d8d8d8;font-size:12px;line-height:24.6px}
.f-about{left:804px;top:3535px;width:244px;color:#c9c9c9;font-size:11px;line-height:17.8px}
.f-rule{left:148px;top:3701px;width:899px;height:1px;background:#3a3a3a}
.follow{left:150px;top:3746px;color:var(--gold);font-size:11px;font-weight:700}
.social{top:3739px;width:26px;height:26px;border-radius:50%;background:var(--gold)}
.copy{left:700px;width:348px;top:3745px;text-align:right;color:#d8d8d8;font-size:12px}
</style>
</head>
<body>

<!-- hero -->
<div class="abs hero" role="img" aria-label="Sydney harbour skyline with opera house and city towers at sunset"></div>
<div class="abs hero-shade"></div>
<div class="abs brand-mark"></div>
<div class="abs brand">AGENT PIVOLA</div>
<nav class="nav">
  <a class="active" style="left:443px">Sell</a>
  <a style="left:502px">Buy</a>
  <a style="left:571px">Sold</a>
  <a style="left:641px">Lease</a>
  <a style="left:726px">Agents</a>
</nav>
<div class="abs btn-join">Join Agent Pivola</div>
<div class="abs btn-login">Login</div>
<h1 class="abs hero-title">Australia-Wide Real Estate, One Click Away</h1>
<p class="abs hero-sub">Discover your next home with our nationwide listings—covering every state across Australia.</p>
<div class="abs search-tabs"><span class="on">Sell</span><span style="width:70px">Buy</span><span style="width:62px">Sold</span></div>
<div class="abs search-input">Start type to find your address</div>
<div class="abs search-btn">GET PROPERTY ESTIMATE</div>

<!-- featured -->
<section class="abs soft" style="left:0;top:628px;width:1200px;height:671px"></section>
<h2 class="abs section-title" style="left:148px;top:678px">Featured Listings</h2>
<div class="abs rule" style="left:148px;top:732px"></div>
<div class="tabs">
  <span class="on" style="left:855px">For Sale</span>
  <span style="left:942px">For Buy</span>
  <span style="left:1019px">Sold</span>
</div>

<div class="abs arrow" style="left:66px;top:948px"><svg width="14" height="14" viewBox="0 0 14 14"><path d="M9 2 4 7l5 5" fill="none" stroke="#666" stroke-width="1.6"/></svg></div>
<div class="abs arrow" style="left:1088px;top:948px"><svg width="14" height="14" viewBox="0 0 14 14"><path d="M5 2l5 5-5 5" fill="none" stroke="#666" stroke-width="1.6"/></svg></div>

<article class="abs card" style="left:150px">
  <div class="photo" role="img" aria-label="Blue weatherboard family home with lit porch and garden path" style="background:linear-gradient(180deg,#5d6f8e,#3c4760 55%,#4f6b3a)"></div>
  <span class="badge">FOR SALE</span>
  <div class="price">AU$ 950,000</div>
  <div class="addr">18 wendell road larkhaven vic 3016</div>
  <div class="feats">
    <div style="width:92px"><svg width="18" height="16" viewBox="0 0 18 16"><path d="M2 8h14v3a3 3 0 0 1-3 3H5a3 3 0 0 1-3-3zM4 8V3a2 2 0 0 1 4 0" fill="none" stroke="#333" stroke-width="1.3"/></svg>3</div>
    <div style="width:82px"><svg width="18" height="14" viewBox="0 0 18 14"><path d="M2 12V2h14v10M2 8h14M5 8V5h8v3" fill="none" stroke="#333" stroke-width="1.3"/></svg>3</div>
    <div style="width:113px"><svg width="16" height="16" viewBox="0 0 16 16"><rect x="2" y="3" width="12" height="11" fill="none" stroke="#333" stroke-width="1.3"/><path d="M2 6h3V3" fill="none" stroke="#333" stroke-width="1.3"/></svg>400m²</div>
  </div>
</article>
<article class="abs card" style="left:455px">
  <div class="photo" role="img" aria-label="Grey two-storey house under a blue sky with front lawn" style="background:linear-gradient(180deg,#6c9ad4,#b9cde3 40%,#8b9492 62%,#6f8c4a)"></div>
  <span class="badge">FOR SALE</span>
  <div class="price">AU$ 950,000</div>
  <div class="addr">18 wendell road larkhaven vic 3016</div>
  <div class="feats">
    <div style="width:92px"><svg width="18" height="16" viewBox="0 0 18 16"><path d="M2 8h14v3a3 3 0 0 1-3 3H5a3 3 0 0 1-3-3zM4 8V3a2 2 0 0 1 4 0" fill="none" stroke="#333" stroke-width="1.3"/></svg>3</div>
    <div style="width:82px"><svg width="18" height="14" viewBox="0 0 18 14"><path d="M2 12V2h14v10M2 8h14M5 8V5h8v3" fill="none" stroke="#333" stroke-width="1.3"/></svg>3</div>
    <div style="width:113px"><svg width="16" height="16" viewBox="0 0 16 16"><rect x="2" y="3" width="12" height="11" fill="none" stroke="#333" stroke-width="1.3"/><path d="M2 6h3V3" fill="none" stroke="#333" stroke-width="1.3"/></svg>400m²</div>
  </div>
</article>
<article class="abs card" style="left:761px">
  <div class="photo" role="img" aria-label="Modern white house with timber cladding and green lawn" style="background:linear-gradient(180deg,#8fb3de,#e8ecef 45%,#c9b9a4 62%,#5f9a3c)"></div>
  <span class="badge">FOR SALE</span>
  <div class="price">AU$ 950,000</div>
  <div class="addr">18 wendell road larkhaven vic 3016</div>
  <div class="feats">
    <div style="width:92px"><svg width="18" height="16" viewBox="0 0 18 16"><path d="M2 8h14v3a3 3 0 0 1-3 3H5a3 3 0 0 1-3-3zM4 8V3a2 2 0 0 1 4 0" fill="none" stroke="#333" stroke-width="1.3"/></svg>3</div>
    <div style="width:82px"><svg width="18" height="14" viewBox="0 0 18 14"><path d="M2 12V2h14v10M2 8h14M5 8V5h8v3" fill="none" stroke="#333" stroke-width="1.3"/></svg>3</div>
    <div style="width:113px"><svg width="16" height="16" viewBox="0 0 16 16"><rect x="2" y="3" width="12" height="11" fill="none" stroke="#333" stroke-width="1.3"/><path d="M2 6h3V3" fill="none" stroke="#333" stroke-width="1.3"/></svg>400m²</div>
  </div>
</article>
<div class="abs btn-gold" style="left:518px;top:1210px;width:163px;height:42px">View More Litings</div>

<!-- explore -->
<h2 class="abs section-title" style="left:0;width:1200px;text-align:center;top:1355px">Explore Real Estate Listings Across Australia</h2>
<div class="abs rule" style="left:578px;top:1424px"></div>
<div class="abs arrow" style="left:68px;top:1516px"><svg width="14" height="14" viewBox="0 0 14 14"><path d="M9 2 4 7l5 5" fill="none" stroke="#666" stroke-width="1.6"/></svg></div>
<div class="abs arrow" style="left:1091px;top:1516px"><svg width="14" height="14" viewBox="0 0 14 14"><path d="M5 2l5 5-5 5" fill="none" stroke="#666" stroke-width="1.6"/></svg></div>

<div class="abs city" style="left:153px"><div class="pic" role="img" aria-label="Sydney opera house at dusk" style="background:linear-gradient(180deg,#7b5aa8,#c79ad0 45%,#d9c6d6 60%,#2a2f4a)"></div><div class="name">Sydney</div><div class="count">1250 Properities</div></div>
<div class="abs divider" style="left:295px"></div>
<div class="abs city" style="left:302px"><div class="pic" role="img" aria-label="Newcastle bridge lit at night" style="background:linear-gradient(180deg,#2c4a8a,#4c6fb5 45%,#c07a48 65%,#1b2336)"></div><div class="name">Newcastle</div><div class="count">145 Properities</div></div>
<div class="abs divider" style="left:446px"></div>
<div class="abs city" style="left:455px"><div class="pic" role="img" aria-label="Melbourne city skyline over the river" style="background:linear-gradient(180deg,#b8c7d8,#7f8fa0 50%,#4e5a63)"></div><div class="name">Melbourne</div><div class="count">2145 Properities</div></div>
<div class="abs divider" style="left:600px"></div>
<div class="abs city" style="left:609px"><div class="pic" role="img" aria-label="Brisbane river and towers" style="background:linear-gradient(180deg,#6fa4d6,#a9c9e4 45%,#6e8798 70%,#3f6a52)"></div><div class="name">Brisbane</div><div class="count">750 Properities</div></div>
<div class="abs divider" style="left:753px"></div>
<div class="abs city" style="left:763px"><div class="pic" role="img" aria-label="Gold Coast high-rise towers" style="background:linear-gradient(180deg,#9a8a70,#7a6a56 45%,#3e4a52)"></div><div class="name">Gold Coast</div><div class="count">214 Properities</div></div>
<div class="abs divider" style="left:904px"></div>
<div class="abs city" style="left:914px"><div class="pic" role="img" aria-label="Perth light sculpture at sunset" style="background:linear-gradient(180deg,#6a4f8a,#d08a5a 45%,#3a4060)"></div><div class="name">Perth</div><div class="count">6512 Properities</div></div>

<!-- helps -->
<section class="abs soft" style="left:0;top:1739px;width:1200px;height:614px"></section>
<h2 class="abs section-title" style="left:0;width:1200px;text-align:center;top:1784px;line-height:44px">Agent Pivola helps you make<br>better property decisions</h2>
<div class="abs rule" style="left:578px;top:1895px"></div>

<article class="abs help on" style="left:150px">
  <div class="art" role="img" aria-label="Illustration of a couple outside a house with a for sale sign" style="background:linear-gradient(180deg,#cfe6f5,#e8d8a8 60%,#7fb356)"></div>
  <h3>Find homes for sale</h3>
  <p>Lorem ipsum dolor sit amet, cons ectetur adipiscing elit, sed do eius mod tempor incididunt ut labore et dolore magna aliqua</p>
  <div class="btn">View properties for sale</div>
</article>
<article class="abs help" style="left:458px">
  <div class="art" role="img" aria-label="Illustration of a buyer and agent shaking hands in front of a home" style="background:linear-gradient(180deg,#dfe9f0,#c6d6e2 55%,#8fae7a)"></div>
  <h3>Find homes for Buy</h3>
  <p>Lorem ipsum dolor sit amet, cons ectetur adipiscing elit, sed do eius mod tempor incididunt ut labore et dolore magna aliqua</p>
  <div class="btn">View properties for Buy</div>
</article>
<article class="abs help" style="left:766px">
  <div class="art" role="img" aria-label="Illustration of a person researching a house with data cards" style="background:linear-gradient(180deg,#ece8f2,#e7b3a6 55%,#8fb878)"></div>
  <h3>Research sold properties</h3>
  <p>Lorem ipsum dolor sit amet, cons ectetur adipiscing elit, sed do eius mod tempor incididunt ut labore et dolore magna aliqua</p>
  <div class="btn">View Sold properties</div>
</article>

<!-- concierge -->
<div class="abs concierge" role="img" aria-label="Brick family home with green lawn under a cloudy sky"></div>
<div class="abs concierge-shade"></div>
<h2 class="abs c-title">Agent Pivola<br>Concierge</h2>
<div class="abs rule" style="left:150px;top:2507px;background:var(--white)"></div>
<p class="abs c-q" style="top:2541px">Looking buy, rent or sell something unique?</p>
<p class="abs c-q" style="top:2582px">Want competitive developer financing at great rates?</p>
<p class="abs c-text">Lorem ipsum dolor sit amet, cons ectetur adipiscing elit, sed do eius mod tempor incididunt ut labore et dolore magna aliqua</p>
<div class="abs btn-gold" style="left:152px;top:2692px;width:141px;height:38px">Find Out More</div>

<!-- sell -->
<div class="abs sell-box"></div>
<div class="abs sell-photo" role="img" aria-label="Family with children running into a bright new home"></div>
<p class="abs sell-label">SELL YOUR PROPERTY</p>
<h2 class="abs sell-title">Sell your property with<br>Australia’s number<br>one agency</h2>
<p class="abs sell-text">Lorem ipsum dolor sit amet, cons ectetur adipiscing elit, sed do eius mod tempor incididunt ut labore et dolore magna aliqua</p>
<div class="abs btn-gold" style="left:216px;top:3219px;width:116px;height:40px">Read More</div>

<!-- footer -->
<footer class="abs"></footer>
<div class="abs f-mark"></div>
<div class="abs f-brand">AGENT PIVOLA</div>
<h4 class="abs f-head" style="left:404px">CONTACT US</h4>
<div class="abs f-list" style="left:407px;top:3532px">Shop 2217B<br>Level 1 Harbourgate Shopping Centre<br>87 Quillon Terrace<br>Southport</div>
<h4 class="abs f-head" style="left:677px">MENU</h4>
<div class="abs f-list" style="left:680px;top:3530px">Sell<br>Buy<br>Sold<br>Lease<br>Agents</div>
<h4 class="abs f-head" style="left:804px">ABOUT US</h4>
<p class="abs f-about">Sed ut perspiciatis unde omnis iste natus error sit voluptatem accusantium doloremque laudantium, totam rem aperiam, eaque ipsa quae ab illo inventore veritatis et quasi architecto beatae vitae dicta sunt explicabo. Nemo enim ipsam voluptatem quia voluptas sit aspernatur aut odit aut fugit</p>
<div class="abs f-rule"></div>
<div class="abs follow">FOLLOW US</div>
<div class="abs social" style="left:241px"></div>
<div class="abs social" style="left:269px"></div>
<div class="abs social" style="left:297px"></div>
<div class="abs social" style="left:325px"></div>
<div class="abs social" style="left:353px"></div>
<div class="abs copy">Copyright © 2025 All Rights Reserved</div>

</body>
</html>
```